Boutique Shoe Bag Race wear Business Card Design

We are a new luxury shoe bag, jewellery and race wear store stocking local and international designers. Located in the fashion precinct of beautiful Marlow Beach famous in Sydney Australia. Stocking French jewellery and shoes such as Henri Delacrouxs plus Australian made. Looking at quality and service and looking after the locals and tourists.
Ideas: White background, Black writing in bold engravers, logo in middle of Marlow and Boutique a gold horseshoe (facing upright so the curve is at the bottom) with a black stiletto inside. French clover silver and black border (not irish clover the French lattice type look)
Updates

Marlow Atelier

I open 8/4 so require business card design ASAP.

Please place gold horseshoe facing upwards with the black stiletto inside.

Bold engravers writing for business name.

I will have my phone number tomorrow to update.

Border in similar/same style as attached picture with black/silver clover French design.

Thank you. Nina                                   

Industry/Entity Type

Fashion

Contact Information for Business Card

Marlow Atelier
Boutique Owner Nina Pellard
41B Tilbury Lane
Marlow Beach NSW 2094 Australia
0471392605
02 **** *TBA
info@marlowatelier.com.au
Friendwall.com/MarlowAtelier
www.marlowatelier.com.au

Font styles to use
Other font styles liked:
• Bold Engravers

Requirements
Must have
• Info on one side including business name and logo with black stiletto and gold horse shoe. reverse side with French clover border and Larger name Marlow Atelier with logo in centre.
Should not have
• irish clover
French script
horseshoe upside down

```html
<!DOCTYPE html>
<html lang="en">
<head>
<meta charset="utf-8">
<title>Marlow Atelier – Business Card</title>
<link rel="stylesheet" href="https://fonts.googleapis.com/css2?family=Cinzel:wght@700&family=Mulish:wght@400;700&display=swap">
<style>
  :root {
    --stage: #ecebe8;
    --card-white: #ffffff;
    --ink: #111111;
    --ink-soft: #2a2a2a;
    --lattice-dark: #1f1f1f;
    --lattice-light: #3a3a3a;
    --silver-light: #e6e6e6;
    --silver-mid: #b9b9b9;
    --silver-dark: #8f8f8f;
    --gold: #b8862e;
    --icon-grey: #8a8a8a;
  }
  * { box-sizing: border-box; margin: 0; padding: 0; }
  html, body {
    width: 1200px; height: 1000px; overflow: hidden;
    background: var(--stage);
  }
  .canvas { position: relative; width: 1200px; height: 1000px; }
  .card {
    position: absolute; left: 190px; width: 820px; height: 440px;
    box-shadow: 0 6px 18px rgba(0,0,0,.18);
  }
  /* Reverse side */
  .card--reverse { top: 40px; }
  .lattice-border {
    position: absolute; inset: 0;
    background: linear-gradient(135deg, var(--lattice-light), var(--lattice-dark));
  }
  .reverse-face {
    position: absolute; inset: 42px; background: var(--card-white);
    display: flex; flex-direction: column; align-items: center; justify-content: center;
  }
  .reverse-name {
    display: flex; align-items: center; gap: 22px;
    font-family: "Cinzel", "Times New Roman", serif; font-weight: 700;
    font-size: 48px; letter-spacing: 3px; color: var(--ink);
  }
  .brand-dot { width: 58px; height: 58px; border-radius: 50%; background: var(--gold); }
  .reverse-web {
    margin-top: 22px;
    font-family: "Mulish", "Century Gothic", sans-serif; font-size: 22px; color: var(--ink-soft);
  }
  /* Front side */
  .card--front { top: 520px; }
  .silver-frame {
    position: absolute; inset: 0;
    background: linear-gradient(135deg, var(--silver-light), var(--silver-mid) 50%, var(--silver-dark));
  }
  .front-face {
    position: absolute; inset: 22px; background: var(--card-white);
    font-family: "Mulish", "Century Gothic", sans-serif; color: var(--ink);
  }
  .front-mark {
    position: absolute; top: 28px; right: 40px;
    width: 64px; height: 64px; border-radius: 50%; background: var(--gold);
  }
  .front-brand {
    position: absolute; top: 62px; left: 40px;
    font-family: "Cinzel", "Times New Roman", serif; font-weight: 700;
    font-size: 40px; letter-spacing: 3px;
  }
  .owner { position: absolute; top: 140px; left: 40px; }
  .owner-name { font-weight: 700; font-size: 30px; }
  .owner-role { font-size: 30px; margin-top: 2px; }
  .contact-list {
    position: absolute; top: 248px; left: 40px; list-style: none;
    font-size: 24px; line-height: 32px;
  }
  .contact-list li { display: flex; align-items: center; gap: 8px; }
  .contact-icon { width: 20px; height: 20px; flex: none; }
  .social-square { width: 18px; height: 18px; background: var(--icon-grey); flex: none; margin-left: 1px; }
  .address {
    position: absolute; top: 140px; right: 40px; text-align: right;
    font-size: 24px; line-height: 32px; color: var(--ink-soft); font-style: normal;
  }
</style>
</head>
<body>
<main class="canvas">

  <section class="card card--reverse" aria-label="Card reverse side">
    <div class="lattice-border" role="img" aria-label="Black and silver French lattice pattern border"></div>
    <div class="reverse-face">
      <div class="reverse-name">
        <span>MARLOW</span><span class="brand-dot" aria-hidden="true"></span><span>ATELIER</span>
      </div>
      <p class="reverse-web">www.marlowatelier.com.au</p>
    </div>
  </section>

  <section class="card card--front" aria-label="Card front side">
    <div class="silver-frame"></div>
    <div class="front-face">
      <span class="front-mark" aria-hidden="true"></span>
      <h1 class="front-brand">MARLOW&nbsp;ATELIER</h1>
      <div class="owner">
        <p class="owner-name">Nina Pellard</p>
        <p class="owner-role">Boutique Owner</p>
      </div>
      <ul class="contact-list">
        <li>
          <svg class="contact-icon" viewBox="0 0 20 20" aria-hidden="true"><rect x="5" y="1.5" width="10" height="17" rx="2" fill="none" stroke="#8a8a8a" stroke-width="1.6"/><line x1="8.5" y1="15.5" x2="11.5" y2="15.5" stroke="#8a8a8a" stroke-width="1.6"/></svg>
          0471392605 02
        </li>
        <li>
          <svg class="contact-icon" viewBox="0 0 20 20" aria-hidden="true"><rect x="1.5" y="4" width="17" height="12" fill="none" stroke="#8a8a8a" stroke-width="1.6"/><polyline points="1.5,4 10,11 18.5,4" fill="none" stroke="#8a8a8a" stroke-width="1.6"/></svg>
          info@marlowatelier.com.au
        </li>
        <li><span class="social-square" aria-hidden="true"></span>Friendwall.com/MarlowAtelier</li>
        <li><span class="social-square" aria-hidden="true"></span>Snapfolio</li>
      </ul>
      <address class="address">
        41B Tilbury Lane<br>
        Marlow Beach<br>
        NSW 2094 Australia
      </address>
    </div>
  </section>

</main>
</body>
</html>
```